Business card design for my company.
I would like the card's background colour to be black. You can also see our web site to get an idea of our brand. https://www.tmwhomecrafting.com.au/
- Name
- Email

```html
<!DOCTYPE html>
<html lang="en">
<head>
<meta charset="UTF-8">
<title>TMW Home Crafting — Business Card</title>
<link rel="stylesheet" href="https://fonts.googleapis.com/css2?family=Montserrat:wght@400;500;700&display=swap">
<style>
  :root {
    --bg: #2a2a2a;
    --card: #1d1d1d;
    --card-sheen: #262626;
    --green: #1f9a46;
    --white: #f2f2f2;
    --muted: #d8d8d8;
  }
  * { margin: 0; padding: 0; box-sizing: border-box; }
  html, body { width: 1200px; height: 801px; overflow: hidden; }
  body {
    background: var(--bg);
    font-family: "Montserrat", sans-serif;
    position: relative;
  }
  .card {
    position: absolute;
    top: 250px;
    width: 520px;
    height: 300px;
    border-radius: 18px;
    background: linear-gradient(135deg, var(--card-sheen) 0%, var(--card) 60%);
    overflow: hidden;
  }
  .card--front { left: 50px; }
  .card--back { left: 630px; }

  .card__fold { position: absolute; inset: 0; }

  .brand {
    position: absolute;
    color: var(--white);
    font-weight: 700;
    letter-spacing: 0.12em;
    text-transform: uppercase;
    line-height: 1.15;
    display: flex;
    align-items: center;
    gap: 10px;
  }
  .brand__mark {
    width: 12px; height: 12px;
    background: var(--green);
    flex: none;
  }
  .card--front .brand { left: 36px; top: 62px; font-size: 20px; }
  .card--back .brand {
    left: 0; right: 0; top: 0; bottom: 0;
    justify-content: center;
    font-size: 30px;
  }

  .person {
    position: absolute;
    right: 56px;
    top: 34px;
    text-align: right;
  }
  .person__name {
    color: var(--green);
    font-weight: 700;
    font-size: 20px;
    letter-spacing: 0.06em;
    text-transform: uppercase;
  }
  .person__title {
    color: var(--white);
    font-size: 13px;
    margin-top: 2px;
  }
  .accent-bar {
    position: absolute;
    right: 0; top: 34px;
    width: 34px; height: 24px;
    background: var(--green);
  }

  .contact {
    position: absolute;
    left: 36px;
    bottom: 34px;
    list-style: none;
    color: var(--white);
    font-size: 13px;
  }
  .contact__item { display: flex; align-items: center; gap: 8px; margin-top: 7px; }
  .contact__icon { width: 11px; height: 11px; flex: none; }
  .contact__highlight { color: var(--green); }
</style>
</head>
<body>

<section class="card card--front" aria-label="Business card front">
  <svg class="card__fold" viewBox="0 0 520 300" aria-hidden="true">
    <polygon points="330,300 420,40 470,40 385,300" fill="#2e2e2e"/>
    <polygon points="420,40 470,40 520,0 470,0" fill="#3a3a3a"/>
  </svg>
  <div class="accent-bar"></div>
  <div class="person">
    <p class="person__name">Dorian Hale</p>
    <p class="person__title">CEO/Founder</p>
  </div>
  <div class="brand"><span class="brand__mark"></span><span>TMW Home<br>Crafting</span></div>
  <ul class="contact">
    <li class="contact__item">
      <svg class="contact__icon" viewBox="0 0 12 12"><path d="M2.5 1 L4.5 1 L5 3.5 L3.8 4.3 Q5 6.8 7.7 8.2 L8.5 7 L11 7.5 L11 9.5 Q11 11 9.5 11 Q1 10 1 2.5 Q1 1 2.5 1Z" fill="var(--green)"/></svg>
      897-512-0194
    </li>
    <li class="contact__item">
      <svg class="contact__icon" viewBox="0 0 12 12"><rect x="0.5" y="2" width="11" height="8" fill="var(--green)"/><path d="M0.5 2 L6 6.5 L11.5 2" stroke="var(--card)" fill="none"/></svg>
      info@tmwhomecrafting.com.au
    </li>
    <li class="contact__item">
      <svg class="contact__icon" viewBox="0 0 12 12"><circle cx="6" cy="6" r="5.5" fill="var(--green)"/><path d="M0.5 6 H11.5 M6 0.5 V11.5" stroke="var(--card)" stroke-width="0.8"/></svg>
      <span>www.<span class="contact__highlight">tmwhomecrafting</span>.com.au</span>
    </li>
  </ul>
</section>

<section class="card card--back" aria-label="Business card back">
  <div class="brand"><span class="brand__mark"></span><span>TMW Home Crafting</span></div>
</section>

</body>
</html>
```